Business Card Design using new attached logo

We are a family run Plumbing and Heating firm looking to improve our company image with an improved business card and new logo.We are looking to keep the company colour (Blue) involved in our design

Reason: New logo added which needs to be incorporated on designs

Industry/Entity Type

Business

Contact Information for Business Card

See attachment of all info required.

Requirements
Must have
• We have just picked a new company logo which is attached.
• Could you please provide your business card designs using this logo.
• We are looking for the logo on the back as well as the front with all the info required

```html
<!DOCTYPE html>
<html lang="en">
<head>
<meta charset="utf-8">
<title>Kestrel Services – Business Card</title>
<link rel="stylesheet" href="https://fonts.googleapis.com/css2?family=Cinzel:wght@600&family=Source+Sans+3:ital,wght@0,400;0,600;0,700;1,400&display=swap">
<style>
  :root {
    --stage: #333333;
    --paper: #ffffff;
    --navy: #1f3b73;
    --blue-mid: #2f64a8;
    --blue-light: #3f82c6;
    --rule: #b9bcc2;
    --ink: #222222;
    --label: #1f3b73;
  }
  * { margin: 0; padding: 0; box-sizing: border-box; }
  html, body {
    width: 1200px; height: 907px; overflow: hidden;
    background: var(--stage);
  }
  .canvas { position: relative; width: 1200px; height: 907px; }

  .card {
    position: absolute; left: 300px; width: 600px; height: 343px;
    box-shadow: 0 4px 10px rgba(0,0,0,0.55);
    overflow: hidden;
  }
  .card--front { top: 91px; background: var(--paper); }
  .card--back {
    top: 472px;
    background: radial-gradient(ellipse 60% 75% at 50% 45%, var(--blue-light) 0%, var(--blue-mid) 45%, var(--navy) 100%);
  }

  .wordmark {
    position: absolute; left: 0; right: 0; text-align: center;
    font-family: "Source Sans 3", sans-serif; font-weight: 700;
    font-size: 46px; letter-spacing: 1px; line-height: 1;
  }
  .card--front .wordmark { top: 58px; color: var(--navy); }
  .card--back .wordmark { top: 142px; color: var(--paper); }

  .name-band {
    position: absolute; left: 0; right: 0; top: 157px; height: 72px;
    border-top: 2px solid var(--rule); border-bottom: 2px solid var(--rule);
    padding: 3px 0;
    background-clip: content-box;
    background-image: linear-gradient(90deg, var(--navy) 0%, var(--blue-mid) 30%, var(--blue-light) 50%, var(--blue-mid) 70%, var(--navy) 100%);
    text-align: center; color: var(--paper);
    font-family: "Cinzel", serif; font-weight: 600;
  }
  .name-band__name { display: block; font-size: 22px; margin-top: 9px; line-height: 1.1; }
  .name-band__role { display: block; font-size: 17px; line-height: 1.2; }

  .contact {
    position: absolute; left: 0; right: 0; top: 255px; text-align: center;
    font-family: "Source Sans 3", sans-serif; font-size: 14.5px; color: var(--ink);
    line-height: 22.5px;
  }
  .contact__label { color: var(--label); font-weight: 700; }
  .contact__sep { color: var(--label); font-weight: 700; margin: 0 5px; }
  .contact__gap { margin-left: 8px; }

  .tagline {
    position: absolute; left: 0; right: 0; top: 282px; text-align: center;
    font-family: "Source Sans 3", sans-serif; font-style: italic;
    font-size: 16px; color: var(--paper);
  }
</style>
</head>
<body>
<main class="canvas">
  <section class="card card--front" aria-label="Business card front">
    <div class="wordmark">Kestrel Services</div>
    <div class="name-band">
      <span class="name-band__name">Daniel Hartley</span>
      <span class="name-band__role">Director</span>
    </div>
    <div class="contact">
      <p>Kestrel Services Ltd, 14 Mill Parade, Ashford Road, Kingston, KT14AB</p>
      <p><span class="contact__label">P :</span> 020 7946 0321
        <span class="contact__label contact__gap">F :</span> 020 7946 0587
        <span class="contact__label contact__gap">C :</span> 07700900412</p>
      <p>danielhartley@kestrelservicesltd.co.uk<span class="contact__sep">||</span>www.kestrelservicesltd.co.uk</p>
    </div>
  </section>

  <section class="card card--back" aria-label="Business card back">
    <div class="wordmark">Kestrel Services</div>
    <p class="tagline">Plumbing and Heating Services</p>
  </section>
</main>
</body>
</html>
```